Unique Business Card Design

Unique Business Card design for our orthotic and prosthetic company. Our logo is on our website, color is light blue. Unique shape (artificial leg shaped, vertical, etc..) preferred. Logo, business name, individual name and basic demographics needed.

Industry/Entity Type

Business

Contact Information for Business Card

Logo, Industry, Phone # Logo, "Prosthetic & Orthotic Services" Place to add individual name and contact info

Colors
cee9f5

Requirements
Must have
• The icon must be there, placement of "Prosthetic & Orthotic Services" can be moved
Nice to have
• Like the mix of light blue, and a little darker blue. One design included the icons from my website which was a nice touch

```html
<!DOCTYPE html>
<html lang="en">
<head>
<meta charset="utf-8">
<title>Limbworks Inc. Business Cards</title>
<link rel="stylesheet" href="https://fonts.googleapis.com/css2?family=Arimo:wght@400;700&family=EB+Garamond:ital@1&display=swap">
<style>
  :root {
    --bg: #2b2b2b;
    --card: #ffffff;
    --brand: #1f6cc4;
    --brand-deep: #1a5aa8;
    --text: #555a60;
    --line: #1f6cc4;
  }
  * { box-sizing: border-box; margin: 0; padding: 0; }
  html, body { width: 1200px; height: 950px; overflow: hidden; }
  body {
    background: radial-gradient(ellipse at 45% 45%, #5a5a5a 0%, var(--bg) 70%);
    font-family: "Arimo", Arial, sans-serif;
    position: relative;
  }
  .card {
    position: absolute;
    width: 700px;
    height: 400px;
    background: var(--card);
    border-radius: 22px;
    overflow: hidden;
    box-shadow: 0 10px 30px rgba(0,0,0,.45);
  }
  .card--front { left: 70px; top: 60px; }
  .card--back { left: 430px; top: 490px; }

  .lockup { position: absolute; }
  .lockup__mark {
    position: absolute;
    width: 92px; height: 92px;
    border-radius: 50%;
    background: var(--brand);
  }
  .wordmark {
    color: var(--brand);
    font-weight: 700;
    letter-spacing: .5px;
    white-space: nowrap;
  }
  .tagline {
    font-family: "EB Garamond", Georgia, serif;
    font-style: italic;
    color: var(--brand);
    border-top: 2px solid var(--line);
    white-space: nowrap;
  }

  .card--front .lockup { left: 150px; top: 140px; }
  .card--front .lockup__mark { left: 0; top: 10px; }
  .card--front .lockup__text { position: absolute; left: 110px; top: 8px; }
  .card--front .wordmark { font-size: 40px; }
  .card--front .tagline { font-size: 24px; margin-top: 4px; padding-top: 2px; }

  .back-disc { position: absolute; left: 320px; top: -100px; width: 450px; height: 450px; }

  .card--back .identity { position: absolute; left: 34px; top: 86px; }
  .card--back .wordmark { font-size: 33px; }
  .card--back .tagline { font-size: 21px; margin-top: 3px; padding-top: 1px; }

  .person { position: absolute; left: 34px; top: 188px; }
  .person__name { font-size: 24px; font-weight: 700; color: var(--brand); }
  .person__title { font-size: 15px; color: var(--brand); margin-top: 2px; }

  .contact { position: absolute; left: 34px; top: 250px; color: var(--text); font-size: 15px; line-height: 20px; list-style: none; }
  .contact__address { margin-bottom: 6px; }
  .contact li { display: flex; align-items: center; gap: 8px; height: 21px; }
  .contact svg { width: 14px; height: 14px; fill: var(--brand); flex: none; }
</style>
</head>
<body>

<section class="card card--front" aria-label="Card front">
  <div class="lockup">
    <span class="lockup__mark"></span>
    <div class="lockup__text">
      <div class="wordmark">LIMBWORKS INC.</div>
      <div class="tagline">Prosthetic &amp; Orthotic Services</div>
    </div>
  </div>
</section>

<section class="card card--back" aria-label="Card back">
  <svg class="back-disc" viewBox="0 0 450 450" aria-hidden="true">
    <circle cx="225" cy="225" r="225" fill="var(--brand)"/>
  </svg>

  <div class="identity">
    <div class="wordmark">LIMBWORKS INC.</div>
    <div class="tagline">Prosthetic &amp; Orthotic Services</div>
  </div>

  <div class="person">
    <div class="person__name">Miriam Tolberg</div>
    <div class="person__title">CO LPO</div>
  </div>

  <ul class="contact">
    <li class="contact__address" style="display:block;height:auto">2280 W. 14th St.<br>Riverton, NY 10455</li>
    <li><svg viewBox="0 0 16 16"><path d="M3 1h3l1.5 4-2 1.2a9 9 0 0 0 4.3 4.3L11 8.5l4 1.5v3a2 2 0 0 1-2 2A12 12 0 0 1 1 3a2 2 0 0 1 2-2z"/></svg>555.204.1800</li>
    <li><svg viewBox="0 0 16 16"><path d="M4 0h8a1 1 0 0 1 1 1v14a1 1 0 0 1-1 1H4a1 1 0 0 1-1-1V1a1 1 0 0 1 1-1zm1 2v10h6V2zm3 11a1 1 0 1 0 0 2 1 1 0 0 0 0-2z"/></svg>555.204.3920</li>
    <li><svg viewBox="0 0 16 16"><path d="M4 1h7v4H4zM1 6h14v7h-3v2H4v-2H1zm4 5v3h6v-3z"/></svg>555-7730418</li>
    <li><svg viewBox="0 0 16 16"><path d="M0 3h16v10H0zm1.5 1.5 6.5 5 6.5-5z"/></svg>mtolberg@limbworksinc.com</li>
    <li><svg viewBox="0 0 16 16"><path d="M8 0a8 8 0 1 0 0 16A8 8 0 0 0 8 0zm0 1.5c1 1.2 1.7 3 1.9 5.7H6.1C6.3 4.5 7 2.7 8 1.5zM1.6 8.8h3c.1 2.2.6 4 1.4 5.4A6.5 6.5 0 0 1 1.6 8.8zm4.5 0h3.8c-.2 2.7-.9 4.5-1.9 5.7-1-1.2-1.7-3-1.9-5.7zm5.3 0h3a6.5 6.5 0 0 1-4.4 5.4c.8-1.4 1.3-3.2 1.4-5.4z"/></svg>www.limbworksinc.com</li>
  </ul>
</section>

</body>
</html>
```